Telecommunications/Power civil contractor needs business card design

Were a new telecommunications/power underground civil contractor that is looking for a new business card design. Our company colours are silver or grey and orange. Feel free to use the white background logo or the black background logo.

Target Market(s)

Local contractors, utility companies, private sector mining/energy companies, developers.

Industry/Entity Type

Telecommunications

Contact Information for Business Card

Each card will need the following info:
Persons name:
Title:
E-mail:
Phone number:
Shop Address:
Mailing Address:

Requirements
Must have
• Each card will need the following info:
• Persons name:
• Title:
• E-mail:
• Phone number:
• Shop Address:
• Mailing Address:

```html
<!DOCTYPE html>
<html lang="en">
<head>
<meta charset="utf-8">
<title>Delvin Civil Works – Business Card</title>
<link rel="stylesheet" href="https://fonts.googleapis.com/css2?family=Lato:wght@400;700;900&display=swap">
<style>
  :root {
    --stage: #2a2a2a;
    --card: #f7f7f7;
    --orange: #e4571f;
    --grey: #5b5b5b;
    --grey-light: #8a8a8a;
    --ink: #3a3a3a;
  }
  * { margin: 0; padding: 0; box-sizing: border-box; }
  html, body {
    width: 1200px;
    height: 873px;
    overflow: hidden;
    background: var(--stage);
    font-family: "Lato", Arial, sans-serif;
  }
  .business-card {
    position: absolute;
    left: 180px;
    top: 196px;
    width: 840px;
    height: 480px;
    background: linear-gradient(160deg, #ffffff 0%, var(--card) 60%, #ececec 100%);
    border-radius: 22px;
    overflow: hidden;
  }
  .watermark-circle {
    position: absolute;
    right: 40px;
    top: 70px;
    width: 360px;
    height: 360px;
    border-radius: 50%;
    border: 26px solid var(--orange);
    opacity: 0.07;
  }
  .brand {
    position: absolute;
    left: 60px;
    top: 170px;
    display: flex;
    flex-direction: column;
    align-items: flex-start;
    gap: 18px;
  }
  .brand-dot {
    width: 92px;
    height: 92px;
    border-radius: 50%;
    border: 8px solid var(--orange);
  }
  .brand-name {
    color: var(--orange);
    font-weight: 900;
    font-size: 36px;
    line-height: 1.05;
    letter-spacing: 1px;
    text-transform: uppercase;
  }
  .holder {
    position: absolute;
    right: 44px;
    top: 40px;
    display: flex;
    align-items: baseline;
    gap: 14px;
  }
  .holder-name { color: var(--orange); font-weight: 700; font-size: 26px; }
  .holder-title { color: var(--ink); font-size: 16px; }
  .holder-rule {
    position: absolute;
    right: 0;
    top: 82px;
    width: 470px;
    height: 3px;
    background: linear-gradient(90deg, rgba(228,87,31,0) 0%, var(--orange) 45%);
  }
  .addresses {
    position: absolute;
    right: 44px;
    top: 96px;
    text-align: right;
  }
  .address { margin-bottom: 18px; }
  .address-label { color: var(--grey-light); font-size: 16px; margin-bottom: 2px; }
  .address-line { color: var(--orange); font-weight: 700; font-size: 18px; line-height: 1.3; }
  .contacts {
    position: absolute;
    right: 44px;
    top: 330px;
    display: flex;
    flex-direction: column;
    align-items: flex-end;
    gap: 22px;
  }
  .contact {
    display: flex;
    align-items: center;
    gap: 12px;
    color: var(--ink);
    font-size: 19px;
  }
  .contact-icon { width: 30px; height: 30px; flex: none; }
</style>
</head>
<body>
  <main class="business-card">
    <div class="watermark-circle" aria-hidden="true"></div>

    <div class="brand">
      <div class="brand-dot" aria-hidden="true"></div>
      <div class="brand-name">Delvin<br>Civil Works</div>
    </div>

    <div class="holder">
      <span class="holder-name">Mara Ellison</span>
      <span class="holder-title">Owner / Founder</span>
    </div>
    <div class="holder-rule" aria-hidden="true"></div>

    <div class="addresses">
      <div class="address">
        <div class="address-label">(Mailing)</div>
        <div class="address-line">48 Harlow Lane, Crest Street</div>
        <div class="address-line">Brackenfield, NSW 6190</div>
      </div>
      <div class="address">
        <div class="address-label">(Shop)</div>
        <div class="address-line">Suite 14, Level 3, 9 Kestrel Street</div>
        <div class="address-line">West Fairmont, NSW 2199</div>
      </div>
    </div>

    <div class="contacts">
      <div class="contact">
        <span>1300 555 812</span>
        <svg class="contact-icon" viewBox="0 0 30 30" aria-hidden="true">
          <circle cx="15" cy="15" r="15" fill="var(--orange)"/>
          <path d="M8 12c0-2 2-3.5 7-3.5s7 1.5 7 3.5l-2.5 1-1-2h-7l-1 2z" fill="#fff"/>
          <path d="M10 14h10l1.5 6h-13z" fill="#fff"/>
          <circle cx="15" cy="17" r="1.8" fill="var(--orange)"/>
        </svg>
      </div>
      <div class="contact">
        <span>mara@delvincivil.com.au</span>
        <svg class="contact-icon" viewBox="0 0 30 30" aria-hidden="true">
          <circle cx="15" cy="15" r="15" fill="var(--orange)"/>
          <rect x="7.5" y="10" width="15" height="10.5" rx="1" fill="#fff"/>
          <path d="M7.8 10.5l7.2 5.5 7.2-5.5" fill="none" stroke="var(--orange)" stroke-width="1.4"/>
        </svg>
      </div>
    </div>
  </main>
</body>
</html>
```